Business Card Design

We are a new company that grows and processes olives. We will be producing both olive oil and table olives. We will add grapes and wine making in about five years and hope to start a small restaurant with an observation window overlooking our olive processing area.
The design we have in mind is one that could be adapted to bottle lables for our olive products. Our thoughts are an oval design showing a night time view of a bay with a family of wolves resting on the shore. We would like a border on top of olive branches with olives. We are pretty open on the rest.

Contact Information for Business Card

Fern Cove Groves
31857 CR 46
Marlow, AL 36912
Dean Hobbs and Rosalind Thorne

```html
<!DOCTYPE html>
<html lang="en">
<head>
<meta charset="utf-8">
<title>Fern Cove Groves – Business Card</title>
<link href="https://fonts.googleapis.com/css2?family=Source+Sans+3:wght@400;700&display=swap" rel="stylesheet">
<style>
  :root {
    --page-bg: #ece9e3;
    --card-white: #ffffff;
    --card-tint: #f1f2ee;
    --olive-green: #8db33a;
    --olive-light: #b7d160;
    --olive-pale: #d6e69b;
    --olive-dark: #3f5a17;
    --text-white: #ffffff;
    --oil-gold: #c9cf2a;
    --herb-green: #6f8a3c;
  }
  * { margin: 0; padding: 0; box-sizing: border-box; }
  html, body {
    width: 1200px;
    height: 1023px;
    overflow: hidden;
    background: var(--page-bg);
    font-family: "Source Sans 3", "Helvetica Neue", Arial, sans-serif;
  }
  .stage {
    width: 1200px;
    height: 1023px;
    display: flex;
    align-items: center;
    justify-content: center;
  }
  .business-card {
    position: relative;
    width: 900px;
    height: 514px;
    background: linear-gradient(160deg, var(--card-white) 0%, var(--card-tint) 100%);
    overflow: hidden;
    box-shadow: 0 14px 40px rgba(0,0,0,0.18);
  }
  .product-photo {
    position: absolute;
    top: 0;
    right: 0;
    width: 380px;
    height: 430px;
    background:
      radial-gradient(ellipse at 55% 30%, var(--oil-gold) 0%, rgba(201,207,42,0.55) 30%, rgba(255,255,255,0) 60%),
      radial-gradient(ellipse at 35% 75%, var(--herb-green) 0%, rgba(111,138,60,0.4) 30%, rgba(255,255,255,0) 60%),
      linear-gradient(180deg, #f4f5f0 0%, #e6e9dc 100%);
  }
  .brand {
    position: absolute;
    left: 70px;
    top: 175px;
    display: flex;
    align-items: center;
    gap: 18px;
  }
  .brand-dot {
    width: 62px;
    height: 62px;
    border-radius: 50%;
    background: var(--olive-green);
  }
  .brand-name {
    font-size: 58px;
    font-weight: 700;
    color: var(--olive-green);
    letter-spacing: -0.5px;
  }
  .contact-band {
    position: absolute;
    left: 0;
    bottom: 0;
    width: 100%;
    height: 110px;
    background: linear-gradient(90deg, var(--olive-green) 0%, var(--olive-light) 100%);
    border-top: 8px solid var(--olive-pale);
    padding: 14px 0 0 70px;
  }
  .contact-name {
    font-size: 26px;
    line-height: 1.05;
    color: var(--olive-dark);
  }
  .contact-address {
    font-size: 26px;
    line-height: 1.1;
    color: var(--text-white);
  }
</style>
</head>
<body>
  <main class="stage">
    <section class="business-card">
      <div class="product-photo" role="img" aria-label="Photograph of olive oil carafes with green olives, olive leaves and herb sprigs"></div>

      <div class="brand">
        <span class="brand-dot"></span>
        <span class="brand-name">Fern Cove Groves</span>
      </div>

      <div class="contact-band">
        <p class="contact-name">Dean Hobbs</p>
        <p class="contact-name">Rosalind Thorne</p>
        <p class="contact-address">31857 CR 46 Marlow, AL 36912</p>
      </div>
    </section>
  </main>
</body>
</html>
```